Stylish business cards for KV7

To create an appealing and professional business card design for a WOMEN Owned Construction Supply Company.
2 sided card. Incorporate brand elements, curvy, colorful, sleek and bright. No solid white background. attached samples of styles added shapes/ribbons. Want something with that WOW that looks awesome, factor. It is a new logo, so feel free to mess with logo colors in the blue and teal factors that can look good with both dark and light background. If you want to try a watermark with just the KV7, without the "Supply" that might look cool to.

Industry/Entity Type

Women owned construction supply company

Contact Information for Business Card

Name, Title, and phone number and email, web page. maybe spot for qr code.

Font styles to use
Sans Serif

Requirements
Nice to have
• would love to see colors, maybe stylish ribbon dividers or some sort of 2 or 3 tone color card that compliments logo.
Should not have
• Please do not have all white background. Do not include Home/reale state/ or building images.

```html
<!DOCTYPE html>
<html lang="en">
<head>
<meta charset="UTF-8">
<title>KV7 Supply Business Cards</title>
<link href="https://fonts.googleapis.com/css2?family=Poppins:wght@400;500;600;700&display=swap" rel="stylesheet">
<style>
  :root {
    --stage: #2b2b2d;
    --slate: #6b8096;
    --slate-text: #d9e0e8;
    --navy: #1f3a5f;
    --ink: #2a3f63;
    --teal: #2a9cc4;
    --white: #ffffff;
    --watermark: #eef0f3;
    --muted: #3a3a3a;
  }
  * { margin: 0; padding: 0; box-sizing: border-box; }
  html, body { width: 1200px; height: 875px; overflow: hidden; }
  body {
    background: var(--stage);
    font-family: "Poppins", sans-serif;
    position: relative;
  }
  .card {
    position: absolute;
    top: 282px;
    width: 540px;
    height: 310px;
    border-radius: 18px;
    overflow: hidden;
  }
  .card-front {
    left: 40px;
    background: var(--slate);
    display: flex;
    align-items: center;
    justify-content: center;
  }
  .brand {
    font-family: "Poppins", sans-serif;
    font-weight: 600;
    white-space: nowrap;
  }
  .card-front .brand {
    font-size: 52px;
    color: var(--slate-text);
  }
  .card-back {
    left: 620px;
    background: var(--white);
  }
  .card-back .watermark {
    position: absolute;
    left: 40px;
    top: 60px;
    font-size: 150px;
    font-weight: 600;
    color: var(--watermark);
    line-height: 1;
  }
  .card-back .brand {
    position: absolute;
    right: 40px;
    top: 36px;
    font-size: 34px;
    color: var(--navy);
  }
  .rule-top {
    position: absolute;
    left: 150px;
    right: 40px;
    top: 98px;
    height: 1.5px;
    background: var(--navy);
  }
  .person {
    position: absolute;
    left: 40px;
    top: 170px;
  }
  .person .name {
    font-size: 20px;
    font-weight: 700;
    color: var(--ink);
    letter-spacing: 0.3px;
    line-height: 1.1;
  }
  .person .title {
    font-size: 13px;
    color: var(--muted);
  }
  .person .rule {
    margin-top: 6px;
    width: 150px;
    height: 1.5px;
    background: var(--navy);
  }
  .contacts {
    list-style: none;
    margin-top: 8px;
  }
  .contacts li {
    display: flex;
    align-items: center;
    gap: 10px;
    font-size: 12.5px;
    color: var(--muted);
    line-height: 1.45;
  }
  .contacts svg { width: 11px; height: 11px; fill: var(--teal); flex: none; }
  .address {
    position: absolute;
    right: 40px;
    top: 150px;
    text-align: right;
    font-size: 12.5px;
    color: var(--muted);
    line-height: 1.35;
  }
  .ribbon {
    position: absolute;
    left: 0;
    bottom: 0;
    width: 540px;
    height: 310px;
  }
</style>
</head>
<body>
  <section class="card card-front" aria-label="Card front">
    <div class="brand">KV7 Supply</div>
  </section>

  <section class="card card-back" aria-label="Card back">
    <svg class="ribbon" viewBox="0 0 540 310" aria-hidden="true">
      <polygon points="540,198 540,216 250,310 190,310" fill="var(--teal)"/>
      <polygon points="540,212 540,310 230,310" fill="var(--navy)"/>
    </svg>
    <div class="watermark" aria-hidden="true">KV7</div>
    <div class="brand">KV7 Supply</div>
    <div class="rule-top"></div>

    <div class="address">
      42 Meridian Court<br>
      Halden, NJ 07000 USA
    </div>

    <div class="person">
      <div class="name">DANIEL REYES</div>
      <div class="title">General Manager</div>
      <div class="rule"></div>
      <ul class="contacts">
        <li><svg viewBox="0 0 24 24"><path d="M6.6 10.8a15 15 0 0 0 6.6 6.6l2.2-2.2a1 1 0 0 1 1-.25 11.4 11.4 0 0 0 3.6.6 1 1 0 0 1 1 1V20a1 1 0 0 1-1 1A17 17 0 0 1 3 4a1 1 0 0 1 1-1h3.5a1 1 0 0 1 1 1c0 1.25.2 2.45.6 3.6a1 1 0 0 1-.25 1z"/></svg>+1.555.010.246</li>
        <li><svg viewBox="0 0 24 24"><path d="M2 5h20v14H2z M2 5l10 8 10-8" /></svg>name@kv7supply.com</li>
        <li><svg viewBox="0 0 24 24"><circle cx="12" cy="12" r="10"/></svg>www.kv7supply.com</li>
      </ul>
    </div>
  </section>
</body>
</html>
```